Web Design for a Biotech Consulting Firm

We need a web site design for a new business based in Philadelphia called Verantel Dx. This is a consulting firm that will serve medical diagnostics industry, which is part of the life science/healthcare industry focusing on developing and marketing products that help in early detection, monitoring or management of diseases. Our consulting firm will help medical diagnostic companies to overcome key challenges in designing, evaluating and marketing new products.Our company name is Verantel Dx. Verantel is Latin word for "something" Dx represents diagnostics. The idea behind the name is that we help companies to transform the original, early product ideas ("nothing") into "something"; which is a product with full clinical utility that will help to improve health and well-being.The web site should use the visual feel of the logo (attached), be modern, simple and clean looking and represent creativity, innovation, scientific thinking and progress.
Updates

Wix Design is acceptable

Industry/Entity Type

Biotechnology

Coding

Coded - Design and coding required

Number of Pages Required

1 page

Font styles to use
Sans Serif

Requirements
Must have
• simple, clean look couple of pages
Should not have
• a lot of pages

```html
<!DOCTYPE html>
<html lang="en">
<head>
<meta charset="utf-8">
<title>Verantel Dx — Diagnostics Consulting</title>
<link href="https://fonts.googleapis.com/css2?family=Lato:wght@400;700;900&family=Open+Sans:wght@400;600;700&display=swap" rel="stylesheet">
<style>
:root{
  --blue:#1f7cf0;
  --blue-dark:#1566d6;
  --blue-deep:#0e5fc9;
  --green:#76c230;
  --green-dark:#5ea629;
  --ink:#222;
  --text:#555;
  --muted:#888;
  --line:#e6e6e6;
  --white:#fff;
}
*{box-sizing:border-box;margin:0;padding:0}
html,body{width:1200px;height:4269px;overflow:hidden}
body{position:relative;font-family:"Open Sans",sans-serif;color:var(--text);background:var(--white)}
.abs{position:absolute}
h1,h2,h3,h4{font-family:"Lato",sans-serif;color:var(--ink)}
a{color:inherit;text-decoration:none}

/* header */
.site-header{position:absolute;left:0;top:0;width:1200px;height:138px;background:#fff;border-bottom:1px solid var(--line)}
.brand{position:absolute;left:111px;top:42px;display:flex;align-items:center;gap:10px;font-family:"Lato",sans-serif;font-size:24px;font-weight:700;color:var(--blue)}
.brand-mark{width:16px;height:16px;background:var(--blue)}
.main-nav{position:absolute;left:408px;top:58px;display:flex;gap:28px;font-family:"Lato",sans-serif;font-weight:700;font-size:17px;color:#222}

/* hero */
.hero{position:absolute;left:0;top:138px;width:1200px;height:483px;background:linear-gradient(90deg,#f6f7f9,#eef0f3 60%,#f4f5f7)}
.hero-title{position:absolute;left:112px;top:135px;font-size:54px;font-weight:700}
.hero-title span{color:var(--blue)}
.hero-lead{position:absolute;left:112px;top:212px;width:370px;font-size:17px;line-height:35px;color:#444}
.btn{display:inline-flex;align-items:center;gap:6px;font-family:"Lato",sans-serif;font-weight:700;font-size:16px;color:#fff}
.btn-blue{position:absolute;left:112px;top:308px;width:178px;height:51px;justify-content:center;background:var(--blue)}
.hero-art{position:absolute;left:505px;top:60px;width:695px;height:430px;background:linear-gradient(120deg,rgba(200,205,214,.35),rgba(236,238,241,.2))}
.product-jar{position:absolute;left:818px;top:250px;width:222px;height:452px;border-radius:34px;background:linear-gradient(180deg,#f1f3f6 0%,#f7b25a 22%,#f5a442 70%,#e8923a 100%)}
.category-bar{position:absolute;left:0;top:621px;width:1200px;height:73px;background:var(--green)}
.category-bar ul{list-style:none;display:flex;gap:12px;position:absolute;left:112px;top:18px;font-family:"Lato",sans-serif;font-weight:700;font-size:17px;color:#fff}
.category-bar li{padding:8px 14px}
.category-bar li.active{background:var(--green-dark)}

/* welcome */
.blue-wedge{position:absolute;left:0;top:0;width:1200px;height:4269px}
.section-title{position:absolute;left:0;width:1200px;text-align:center;font-size:44px;font-weight:700}
.section-sub{position:absolute;left:0;width:1200px;text-align:center;font-size:15px}
.on-blue{color:#fff}
.service-card{position:absolute;width:457px;height:196px;background:#fff;box-shadow:0 3px 10px rgba(0,0,0,.12)}
.service-card svg{position:absolute;left:26px;top:34px}
.service-card h3{position:absolute;left:134px;top:34px;font-size:23px;font-weight:700}
.service-card p{position:absolute;left:134px;top:80px;width:296px;font-size:15px;line-height:30px;text-align:justify;color:#444}

/* about */
.video-frame{position:absolute;left:66px;top:1458px;width:433px;height:390px;border:4px solid #fff}
.video-frame-accent{position:absolute;left:430px;top:1596px;width:69px;height:252px;border-right:3px solid var(--green);border-bottom:3px solid var(--green)}
.video-still{position:absolute;left:111px;top:1505px;width:467px;height:296px;background:linear-gradient(135deg,#c9d6e8,#8fa9c8 45%,#5e7aa4)}
.play{position:absolute;left:315px;top:1632px}
.about-title{position:absolute;left:660px;top:1448px;font-size:44px;font-weight:700}
.about-lead{position:absolute;left:660px;top:1520px;width:429px;font-family:"Lato",sans-serif;font-size:22px;line-height:32px;color:var(--green);text-align:justify}
.about-body{position:absolute;left:660px;top:1610px;width:429px;font-size:15px;line-height:31px;text-align:justify;color:#555}
.btn-green{position:absolute;left:660px;top:1801px;width:177px;height:52px;justify-content:center;background:var(--green)}

/* team */
.team-card{position:absolute;top:2093px;width:484px;height:175px;border:1px solid #eee;background:#fff}
.avatar{position:absolute;left:20px;top:22px;width:133px;height:133px;border-radius:50%;border:3px solid var(--blue);background:linear-gradient(160deg,#dfe6ee,#b9c6d4)}
.team-card h4{position:absolute;left:186px;top:34px;font-size:18px;font-weight:400;letter-spacing:.5px}
.team-card p{position:absolute;left:186px;top:66px;width:270px;font-size:12px;line-height:22px;color:#777}
.team-card a{position:absolute;left:186px;top:118px;font-family:"Lato",sans-serif;font-weight:700;font-size:14px;color:var(--green);text-decoration:underline}
.divider{position:absolute;left:111px;top:2380px;width:978px;height:1px;background:var(--line)}

/* news */
.news-card{position:absolute;top:2610px;width:310px;height:377px;background:#fff;box-shadow:0 2px 8px rgba(0,0,0,.1)}
.news-photo{position:absolute;left:6px;top:6px;width:298px;height:198px}
.date-badge{position:absolute;right:30px;top:148px;width:50px;height:60px;background:var(--green);color:#fff;text-align:center;font-family:"Lato",sans-serif}
.date-badge b{display:block;font-size:24px;line-height:34px}
.date-badge span{font-size:15px}
.news-card h3{position:absolute;left:24px;top:232px;font-size:17px;font-weight:400;color:#222}
.news-card p{position:absolute;left:24px;top:272px;width:265px;font-size:13px;line-height:24px;color:#888}
.news-meta{position:absolute;left:24px;top:345px;width:270px;display:flex;align-items:center;gap:8px;font-size:11px;color:#888}
.news-meta .more{margin-left:auto;color:var(--green)}

/* testimonials */
.quote-card{position:absolute;top:3206px;width:302px;height:203px;background:#fff;box-shadow:0 2px 8px rgba(0,0,0,.12);text-align:center}
.quote-card svg{margin-top:22px}
.quote-card p{width:260px;margin:10px auto 0;font-size:12px;line-height:22px;color:#666}
.quote-face{position:absolute;top:3367px;width:82px;height:82px;border-radius:50%;border:3px solid #fff;background:linear-gradient(160deg,#e3e8ee,#a7b6c7)}
.quote-name{position:absolute;top:3469px;width:302px;text-align:center;font-size:14px}
.quote-name b{font-weight:700}
.carousel-arrow{position:absolute;top:3284px;width:48px;height:48px;border-radius:50%;background:#fff;border:1px solid #ddd}
.dots{position:absolute;left:530px;top:3550px;display:flex;gap:14px}
.dots i{display:block;width:16px;height:16px;border-radius:50%;border:2px solid #fff}
.dots i.on{background:var(--green);border-color:var(--green)}

/* footer */
.footer{color:#fff;font-size:14px}
.footer h4{position:absolute;color:#fff;font-size:18px;font-weight:700}
.footer p{position:absolute;line-height:26px}
.foot-rule{position:absolute;left:111px;top:3887px;width:978px;height:1px;background:rgba(255,255,255,.3)}
.foot-rule.top{top:3635px}
.foot-list{position:absolute;list-style:none;font-size:14px;line-height:30px}
.foot-list li::before{content:"»";margin-right:12px}
.socials{position:absolute;left:898px;top:3992px;display:flex;gap:10px}
.socials i{display:block;width:36px;height:36px;border-radius:50%;border:2px solid #fff}
.copyright{position:absolute;left:0;top:4200px;width:1200px;height:69px;background:var(--blue-deep);color:#fff;text-align:center;line-height:69px;font-size:16px}
</style>
</head>
<body>

<svg class="blue-wedge" width="1200" height="4269" aria-hidden="true">
  <defs>
    <linearGradient id="welcomeBlue" x1="0" y1="0" x2="1" y2="1">
      <stop offset="0" stop-color="#2a86f2"/><stop offset="1" stop-color="#1870e8"/>
    </linearGradient>
  </defs>
  <polygon points="0,694 1200,694 1200,845 0,2005" fill="url(#welcomeBlue)"/>
  <polygon points="1200,3099 1200,4200 0,4200 0,3679" fill="#1f7cf0"/>
</svg>

<header class="site-header">
  <div class="brand"><span class="brand-mark"></span>Verantel Dx</div>
  <nav class="main-nav">
    <a>HOME</a><a>ABOUT</a><a>EXPERIENCE</a><a>SERVICES</a><a>TEAM</a><a>NEWS</a><a>CONTACT</a>
    <svg width="18" height="18" viewBox="0 0 18 18"><circle cx="7" cy="7" r="5.5" fill="none" stroke="#222" stroke-width="2.4"/><line x1="11" y1="11" x2="16" y2="16" stroke="#222" stroke-width="2.6"/></svg>
  </nav>
</header>

<section class="hero">
  <div class="hero-art" role="img" aria-label="Line illustration of medical and laboratory equipment"></div>
  <h1 class="hero-title">Verantel <span>Dx</span></h1>
  <p class="hero-lead">Lorem ipsum dolor sit amet, consectetur adipiscing eiusmod tempor.</p>
  <a class="btn btn-blue">READ MORE
    <svg width="15" height="15" viewBox="0 0 16 16"><circle cx="8" cy="8" r="7.5" fill="#fff"/><path d="M6 4.5 9.5 8 6 11.5" stroke="#1f7cf0" stroke-width="2.2" fill="none"/></svg></a>
</section>
<nav class="category-bar">
  <ul><li class="active">BIOLOGICS</li><li>PHARMACEUTICALS</li><li>DEVICES</li><li>BIOSIMILARS</li></ul>
</nav>
<div class="product-jar" role="img" aria-label="Glass jar filled with orange capsules"></div>

<h2 class="section-title on-blue" style="top:778px">Welcome To Verantel Dx</h2>
<p class="section-sub on-blue" style="top:843px">Lorem ipsum dolor sit amet, consectetur adipiscing elit, sed do eiusmod tempor incididunt ut</p>

<article class="service-card" style="left:128px;top:911px">
  <svg width="86" height="86" viewBox="0 0 86 86" fill="none" stroke="#1f7cf0" stroke-width="2.5"><circle cx="36" cy="36" r="26"/><circle cx="36" cy="36" r="17"/><line x1="55" y1="55" x2="78" y2="78" stroke-width="6"/><circle cx="32" cy="34" r="4"/><circle cx="42" cy="40" r="3"/></svg>
  <h3>Diseases Detection</h3>
  <p>Lorem ipsum dolor sit amet, consectetur adipiscing elit, sed do eiusmod tempor incididunt ut labore...</p>
</article>
<article class="service-card" style="left:616px;top:911px">
  <svg width="86" height="86" viewBox="0 0 86 86" fill="none" stroke="#1f7cf0" stroke-width="2.5"><rect x="6" y="6" width="74" height="60" rx="3"/><line x1="6" y1="54" x2="80" y2="54"/><path d="M14 34h14l6-12 8 22 6-10h24" stroke="#76c230"/><line x1="34" y1="66" x2="30" y2="78"/><line x1="52" y1="66" x2="56" y2="78"/><line x1="24" y1="78" x2="62" y2="78"/></svg>
  <h3>Monitoring Diseases</h3>
  <p>Lorem ipsum dolor sit amet, consectetur adipiscing elit, sed do eiusmod tempor incididunt ut labore...</p>
</article>
<article class="service-card" style="left:128px;top:1135px">
  <svg width="86" height="86" viewBox="0 0 86 86" fill="none" stroke="#1f7cf0" stroke-width="2.5"><rect x="12" y="24" width="62" height="40" rx="3"/><path d="M4 70h78l-6 8H10z"/><circle cx="43" cy="20" r="9" stroke="#76c230"/><path d="M30 46c2-10 24-10 26 0" stroke="#76c230"/></svg>
  <h3>Management of Diseases</h3>
  <p>Lorem ipsum dolor sit amet, consectetur adipiscing elit, sed do eiusmod tempor incididunt ut labore...</p>
</article>
<article class="service-card" style="left:616px;top:1135px">
  <svg width="86" height="86" viewBox="0 0 86 86" fill="none" stroke="#1f7cf0" stroke-width="2.5"><path d="M22 54 56 20l10 10-34 34z"/><line x1="61" y1="25" x2="76" y2="10"/><line x1="70" y1="6" x2="80" y2="16"/><line x1="27" y1="59" x2="10" y2="76"/><line x1="36" y1="40" x2="42" y2="46" stroke="#76c230"/><line x1="44" y1="32" x2="50" y2="38" stroke="#76c230"/></svg>
  <h3>Full Scope of Needs</h3>
  <p>Lorem ipsum dolor sit amet, consectetur adipiscing elit, sed do eiusmod tempor incididunt ut labore...</p>
</article>

<div class="video-frame"></div>
<div class="video-frame-accent"></div>
<div class="video-still" role="img" aria-label="Video still of a patient monitor in a hospital room"></div>
<svg class="play" width="60" height="60" viewBox="0 0 60 60" aria-hidden="true"><circle cx="30" cy="30" r="28" fill="#fff" opacity=".9"/><path d="M24 18 42 30 24 42z" fill="#1f7cf0"/></svg>

<h2 class="about-title">About Verantel Dx</h2>
<p class="about-lead">Our consulting firm will help medical diagnostic companies.</p>
<p class="about-body">Lorem ipsum dolor sit amet, consectetur adipiscing elit, sed do eiusmod tempor incididunt ut labore et dolore magna aliqua. Quis ipsum suspendisse ultrices gravida. Risus commodo viverra maecenas afacilisis. Lorem ipsum dolor sit amet, consectetur adipiscing elit.</p>
<a class="btn btn-green">READ MORE
  <svg width="15" height="15" viewBox="0 0 16 16"><circle cx="8" cy="8" r="7.5" fill="#fff"/><path d="M6 4.5 9.5 8 6 11.5" stroke="#76c230" stroke-width="2.2" fill="none"/></svg></a>

<h2 class="section-title" style="top:1967px">Meet Our Team</h2>
<p class="section-sub" style="top:2036px;font-size:14px;color:#666">We understand the success secrets of the world's most successful team.</p>

<article class="team-card" style="left:99px">
  <div class="avatar" role="img" aria-label="Portrait of team member"></div>
  <h4>MARCO LINDELL</h4>
  <p>Nemo enim ipsam voluptem quia voluptas sit aspernatur aut odit aut fugit sed quia</p>
  <a>READ MORE ›</a>
</article>
<article class="team-card" style="left:616px">
  <div class="avatar" role="img" aria-label="Portrait of team member"></div>
  <h4>NADIA ORWEN</h4>
  <p>Nemo enim ipsam voluptem quia voluptas sit aspernatur aut odit aut fugit sed quia</p>
  <a>READ MORE ›</a>
</article>

<div class="divider"></div>

<h2 class="section-title" style="top:2459px">From The News</h2>
<p class="section-sub" style="top:2552px;font-size:14px;color:#666">Lorem ipsum dolor sit amet, consectetur adipiscing elit, sed do eiusmod tempor incididunt ut labore.</p>

<article class="news-card" style="left:108px">
  <div class="news-photo" role="img" aria-label="Hospital ward with beds and equipment" style="background:linear-gradient(135deg,#c7d2dc,#8a9aab)"></div>
  <div class="date-badge"><b>12</b><span>JUN</span></div>
  <h3>Shrinking From Toil and Pain</h3>
  <p>Dignissimos ducimus atque qui blanditiis praesentium voluptatum deleniti...</p>
  <div class="news-meta"><span>Sam Ortis</span>|<span>0 Comments</span><span class="more">More »</span></div>
</article>
<article class="news-card" style="left:446px">
  <div class="news-photo" role="img" aria-label="Doctor with patient at a scanner" style="background:linear-gradient(135deg,#e4e8ee,#aab8c8)"></div>
  <div class="date-badge" style="background:var(--blue)"><b>12</b><span>JUN</span></div>
  <h3>Shrinking From Toil and Pain</h3>
  <p>Dignissimos ducimus atque qui blanditiis praesentium voluptatum deleniti...</p>
  <div class="news-meta"><span>Sam Ortis</span>|<span>0 Comments</span><span class="more">More »</span></div>
</article>
<article class="news-card" style="left:784px">
  <div class="news-photo" role="img" aria-label="Medical staff walking in a hospital corridor" style="background:linear-gradient(135deg,#d9dfe6,#7f93a8)"></div>
  <div class="date-badge"><b>12</b><span>JUN</span></div>
  <h3>Shrinking From Toil and Pain</h3>
  <p>Dignissimos ducimus atque qui blanditiis praesentium voluptatum deleniti...</p>
  <div class="news-meta"><span>Sam Ortis</span>|<span>0 Comments</span><span class="more">More »</span></div>
</article>

<h2 class="section-title" style="top:3101px">Our Testimonials</h2>

<div class="carousel-arrow" style="left:27px"><svg width="46" height="46" viewBox="0 0 46 46"><path d="M26 15 18 23l8 8" stroke="#76c230" stroke-width="2" fill="none"/></svg></div>
<div class="carousel-arrow" style="left:1124px"><svg width="46" height="46" viewBox="0 0 46 46"><path d="M20 15l8 8-8 8" stroke="#76c230" stroke-width="2" fill="none"/></svg></div>

<article class="quote-card" style="left:111px">
  <svg width="40" height="28" viewBox="0 0 40 28"><path d="M2 26V14C2 6 7 2 15 1v5c-4 1-6 4-6 8h6v12zM23 26V14c0-8 5-12 13-13v5c-4 1-6 4-6 8h6v12z" fill="#ddd"/></svg>
  <p>"At vero eos et accusamus et iusto odio dignissimos ducimus qui blanditiis tatum delgd enti atque corrupti quos dolores et quas es fhr ghr molestias"</p>
</article>
<article class="quote-card" style="left:449px">
  <svg width="40" height="28" viewBox="0 0 40 28"><path d="M2 26V14C2 6 7 2 15 1v5c-4 1-6 4-6 8h6v12zM23 26V14c0-8 5-12 13-13v5c-4 1-6 4-6 8h6v12z" fill="#76c230"/></svg>
  <p>"At vero eos et accusamus et iusto odio dignissimos ducimus qui blanditiis tatum delgd enti atque corrupti quos dolores et quas es fhr ghr molestias"</p>
</article>
<article class="quote-card" style="left:787px">
  <svg width="40" height="28" viewBox="0 0 40 28"><path d="M2 26V14C2 6 7 2 15 1v5c-4 1-6 4-6 8h6v12zM23 26V14c0-8 5-12 13-13v5c-4 1-6 4-6 8h6v12z" fill="#ddd"/></svg>
  <p>"At vero eos et accusamus et iusto odio dignissimos ducimus qui blanditiis tatum delgd enti atque corrupti quos dolores et quas es fhr ghr molestias"</p>
</article>
<div class="quote-face" role="img" aria-label="Client portrait" style="left:221px"></div>
<div class="quote-face" role="img" aria-label="Client portrait" style="left:559px"></div>
<div class="quote-face" role="img" aria-label="Client portrait" style="left:897px"></div>
<p class="quote-name" style="left:111px;color:#444"><b>ARJUN BELKAR,</b> <span style="color:#888">Creative Manager</span></p>
<p class="quote-name" style="left:449px;color:#fff"><b>LENA MARSH,</b> Creative Manager</p>
<p class="quote-name" style="left:787px;color:#fff"><b>TOM REDDALE,</b> Creative Manager</p>
<div class="dots"><i></i><i></i><i class="on"></i><i></i><i></i></div>

<footer class="footer">
  <div class="foot-rule top"></div>
  <h4 style="left:111px;top:3715px">ABOUT VERANTEL DX</h4>
  <p style="left:111px;top:3760px;width:440px">Lorem ipsum dolor sit amet, consectetur adipiscing elit, sed do eiusmod tempor incididunt ut labore et dolore magna aliqua. Ut enim ad minim veniam, quis nostrud.</p>

  <h4 style="left:644px;top:3715px">CONTACT DETAILS</h4>
  <p style="left:644px;top:3752px;font-weight:700;font-size:13px">ADDRESS:</p>
  <svg class="abs" style="left:644px;top:3796px" width="14" height="18" viewBox="0 0 14 18"><path d="M7 0a7 7 0 0 0-7 7c0 5 7 11 7 11s7-6 7-11a7 7 0 0 0-7-7z" fill="#fff"/><circle cx="7" cy="7" r="2.5" fill="#1f7cf0"/></svg>
  <p style="left:672px;top:3790px;width:220px;font-size:13px">48 Harlow Lane, Brookfield, Elm County, USA.</p>

  <p style="left:918px;top:3708px;font-weight:700;font-size:13px">PHONE:</p>
  <svg class="abs" style="left:918px;top:3743px" width="14" height="14" viewBox="0 0 14 14"><path d="M3 0 6 3 4.5 5.2c1 2 2.3 3.3 4.3 4.3L11 8l3 3-2 3C5 13 1 9 0 2z" fill="#fff"/></svg>
  <p style="left:946px;top:3737px;font-size:13px">(+1) 215 555 0142</p>
  <p style="left:918px;top:3783px;font-weight:700;font-size:13px">EMAIL:</p>
  <svg class="abs" style="left:918px;top:3820px" width="16" height="12" viewBox="0 0 16 12"><rect width="16" height="12" fill="#fff"/><path d="M0 0 8 7 16 0" stroke="#1f7cf0" stroke-width="1.5" fill="none"/></svg>
  <p style="left:946px;top:3812px;font-size:13px">info@veranteldx.com</p>

  <div class="foot-rule"></div>

  <h4 style="left:111px;top:3943px">QUICK LINKS</h4>
  <ul class="foot-list" style="left:111px;top:3984px"><li>Home</li><li>About Us</li><li>Services</li><li>Our Team</li><li>Contact Us</li></ul>
  <h4 style="left:333px;top:3943px">OTHER LINKS</h4>
  <ul class="foot-list" style="left:333px;top:3984px"><li>News</li><li>Reviews</li><li>Blog Post</li><li>Terms &amp; Conditions</li><li>Privacy Policy</li></ul>
  <h4 style="left:625px;top:3943px">OPENING HOURS</h4>
  <ul class="foot-list" style="left:625px;top:3984px"><li>Mon - Fri: 8.30am-5.30pm</li><li>Sat: 8.30am-12pm</li><li>Sun: Closed</li></ul>
  <h4 style="left:898px;top:3943px">FOLLOW US</h4>
  <div class="socials"><i></i><i></i><i></i><i></i></div>
</footer>

<div class="copyright">Copyrights © 2019 Verantel Dx.&nbsp; All Rights Reserved</div>

</body>
</html>
```